New Business Card Design Project

Need a design that will create an impact / strong impression towards our clients for our business. We are in the lighting business and we do lighting retrofits for large commercial to industrial clientele.

Target Market(s)

Lighting Industry

Industry/Entity Type

Business

Font styles to use
Other font styles liked:
• we would like to use the font on our logo, not sure what it is though..

Requirements
Must have
• Our logo.
Nice to have
• We are open to suggestions that have to do with lighting.

```html
<!DOCTYPE html>
<html lang="en">
<head>
<meta charset="utf-8">
<title>Brightwell Retrofit Group – Business Card</title>
<link rel="stylesheet" href="https://fonts.googleapis.com/css2?family=Montserrat:wght@400;500;600&display=swap">
<style>
  :root {
    --bg: #3a3a3a;
    --green-deep: #1e4a22;
    --green-front-a: #1f5a2a;
    --green-front-b: #17461f;
    --green-bright: #0f8a3f;
    --green-light: #5cc15a;
    --white: #ffffff;
    --text-soft: #e8efe8;
  }
  * { margin: 0; padding: 0; box-sizing: border-box; }
  html, body { width: 1200px; height: 810px; overflow: hidden; }
  body {
    background: var(--bg);
    font-family: "Montserrat", Arial, sans-serif;
    position: relative;
  }
  .card {
    position: absolute;
    width: 560px;
    height: 320px;
    box-shadow: 0 14px 30px rgba(0,0,0,.45);
    overflow: hidden;
  }
  /* Front */
  .card-front {
    left: 130px; top: 70px;
    background: linear-gradient(135deg, var(--green-front-a), var(--green-front-b));
    color: var(--white);
    text-align: center;
  }
  .front-brand {
    position: absolute;
    top: 112px; left: 0; right: 0;
    display: flex; align-items: center; justify-content: center; gap: 12px;
  }
  .brand-square {
    width: 18px; height: 18px;
    background: var(--green-light);
  }
  .brand-name {
    font-weight: 600;
    font-size: 38px;
    letter-spacing: 1px;
    color: var(--white);
  }
  .front-tagline {
    position: absolute;
    top: 166px; left: 0; right: 0;
    font-size: 12px; font-weight: 600; letter-spacing: 2px;
    text-transform: uppercase;
  }
  .front-rule {
    position: absolute; top: 186px; left: 150px; width: 260px; height: 1px;
    background: var(--green-light);
  }
  .front-web {
    position: absolute; bottom: 46px; left: 0; right: 0;
    font-size: 12px; letter-spacing: 1.5px; color: var(--text-soft);
  }
  .front-web span { color: var(--green-light); }

  /* Back */
  .card-back {
    left: 510px; top: 420px;
    background: var(--green-deep);
    color: var(--white);
  }
  .back-logo-panel {
    position: absolute; left: 0; top: 0; bottom: 0; width: 190px;
    background: var(--white);
  }
  .back-notch {
    position: absolute; left: 190px; top: 44px;
    width: 0; height: 0;
    border-top: 10px solid transparent;
    border-bottom: 10px solid transparent;
    border-left: 12px solid var(--white);
  }
  .back-brand {
    position: absolute;
    left: 95px; top: 160px;
    transform: translate(-50%, -50%) rotate(-90deg);
    white-space: nowrap;
    display: flex; align-items: center; gap: 10px;
  }
  .back-brand .brand-name { color: var(--green-deep); font-size: 26px; }
  .back-brand .brand-square { width: 14px; height: 14px; background: var(--green-bright); }
  .back-corner {
    position: absolute; right: 0; bottom: 0;
  }
  .person {
    position: absolute; left: 225px; top: 38px;
  }
  .person-name {
    font-size: 19px; font-weight: 500; color: var(--green-light);
    letter-spacing: .5px; text-transform: uppercase;
  }
  .person-role { font-size: 15px; margin-top: 2px; }
  .address {
    position: absolute; left: 240px; top: 124px;
    font-size: 13px; line-height: 1.5; letter-spacing: .5px;
  }
  .contacts {
    position: absolute; left: 240px; top: 210px;
    list-style: none; font-size: 13px; letter-spacing: .5px;
  }
  .contacts li { display: flex; align-items: center; gap: 10px; line-height: 21px; }
  .contacts svg { width: 11px; height: 11px; fill: var(--green-light); }
</style>
</head>
<body>

<section class="card card-front" aria-label="Business card front">
  <div class="front-brand">
    <span class="brand-square"></span>
    <span class="brand-name">BRIGHTWELL</span>
  </div>
  <p class="front-tagline">Retrofit Group</p>
  <div class="front-rule"></div>
  <p class="front-web">www.<span>brightwellgroup</span>.com</p>
</section>

<section class="card card-back" aria-label="Business card back">
  <div class="back-logo-panel">
    <div class="back-brand">
      <span class="brand-square"></span>
      <span class="brand-name">BRIGHTWELL</span>
    </div>
  </div>
  <div class="back-notch"></div>

  <svg class="back-corner" width="200" height="200" viewBox="0 0 200 200" aria-hidden="true">
    <polygon points="200,0 200,200 0,200" fill="var(--green-bright)"/>
  </svg>

  <div class="person">
    <p class="person-name">Daniel Reyes</p>
    <p class="person-role">Founder</p>
  </div>

  <p class="address">4870 Cedar Avenue,<br>Suite 12 Tempe 85281</p>

  <ul class="contacts">
    <li>
      <svg viewBox="0 0 24 24"><path d="M6.6 10.8c1.4 2.8 3.8 5.1 6.6 6.6l2.2-2.2c.3-.3.7-.4 1-.2 1.1.4 2.3.6 3.6.6.6 0 1 .4 1 1V20c0 .6-.4 1-1 1C10.6 21 3 13.4 3 4c0-.6.4-1 1-1h3.5c.6 0 1 .4 1 1 0 1.3.2 2.5.6 3.6.1.3 0 .7-.2 1z"/></svg>
      0400 555 019
    </li>
    <li>
      <svg viewBox="0 0 24 24"><path d="M2 5h20v14H2z M2 5l10 8 10-8" /></svg>
      info@brightwellgroup.com
    </li>
    <li>
      <svg viewBox="0 0 24 24"><circle cx="12" cy="12" r="10"/></svg>
      www.brightwellgroup.com
    </li>
  </ul>
</section>

</body>
</html>
```